Brightway Haul & Upkeep Services, are a company that offers a 'one stop shop' pre-move clean up a

I have already selected a logo which I would like on the front of the business cards along with phone numbers, web address and email which are:
0487650392
www.brightwayhaul.com.au
brightwayhaulandupkeep@mailbox.example

On the back of the card I would like to list some of the types of service we offer (clean - move - repairs/maintenance) which are:
CLEAN - windows, gutters, solar panels, driveways/paths, carpets.
MOVE - Small/medium size house/office moves, large item pick-up & delivery, yard clean-up and removal.
General maintenance and repairs.

I would like the blue logo on a gray background.

Thanks

```html
<!DOCTYPE html>
<html lang="en">
<head>
<meta charset="utf-8">
<title>Brightway Haul &amp; Upkeep Services – Business Card</title>
<link rel="stylesheet" href="https://fonts.googleapis.com/css2?family=Open+Sans:wght@400;600;700;800&display=swap">
<style>
  :root {
    --page: #e9e7e3;
    --card-light: #f4f4f4;
    --card-mid: #d3d3d3;
    --card-edge: #b9b9b9;
    --brand-blue: #2a6ab4;
    --band-blue: #6b95c2;
    --band-blue-dark: #4f7fb2;
    --ink: #2b2b2b;
    --white: #ffffff;
  }
  * { box-sizing: border-box; margin: 0; padding: 0; }
  html, body { width: 1200px; height: 718px; overflow: hidden; }
  body {
    background: var(--page);
    font-family: "Open Sans", Arial, sans-serif;
    position: relative;
  }
  .card {
    position: absolute;
    top: 194px;
    width: 540px;
    height: 330px;
    border-radius: 4px;
    overflow: hidden;
    background: radial-gradient(ellipse at 50% 40%, var(--card-light) 0%, var(--card-mid) 75%, var(--card-edge) 100%);
    box-shadow: 0 6px 18px rgba(0,0,0,0.22);
  }
  .card--front { left: 40px; }
  .card--back  { left: 620px; }

  /* Brand name lockup */
  .brand {
    display: flex;
    align-items: center;
    gap: 12px;
    color: var(--brand-blue);
    font-weight: 800;
    line-height: 1.05;
  }
  .brand__mark {
    width: 22px; height: 22px;
    background: var(--brand-blue);
    border-radius: 3px;
    flex: none;
  }
  .card--front .brand {
    position: absolute; left: 42px; top: 58px;
    font-size: 31px;
    width: 420px;
  }
  .card--back .brand {
    position: absolute; left: 40px; top: 28px;
    font-size: 26px;
    width: 460px;
  }

  /* Front band */
  .front-band {
    position: absolute; left: 0; bottom: 0;
    width: 540px; height: 150px;
  }
  .contact {
    position: absolute; left: 36px; right: 20px;
    color: var(--white);
  }
  .contact__row {
    display: flex; align-items: center; gap: 24px;
    top: 242px; font-size: 14px;
  }
  .contact__item { display: flex; align-items: center; gap: 7px; white-space: nowrap; }
  .contact__icon { width: 13px; height: 13px; fill: var(--white); }
  .contact__web {
    top: 284px; font-size: 15px; font-weight: 700; letter-spacing: 2.5px;
  }

  /* Back content */
  .services { position: absolute; left: 40px; top: 118px; right: 30px; color: var(--ink); }
  .services__title {
    color: var(--brand-blue);
    font-size: 22px; font-weight: 600; letter-spacing: 3px;
    margin-bottom: 12px;
  }
  .service-list { list-style: none; font-size: 14px; line-height: 1.4; }
  .service-list li { display: grid; grid-template-columns: 62px 1fr; margin-bottom: 6px; }
  .service-list__label { color: var(--brand-blue); font-weight: 700; }
  .services__general {
    color: var(--brand-blue);
    font-size: 17px; font-weight: 600; letter-spacing: 2px;
    margin-top: 6px;
  }
</style>
</head>
<body>

  <section class="card card--front" aria-label="Business card front">
    <div class="brand">
      <span class="brand__mark"></span>
      <span class="brand__name">Brightway Haul &amp; Upkeep Services</span>
    </div>

    <svg class="front-band" viewBox="0 0 540 150" aria-hidden="true">
      <polygon points="0,44 540,0 540,150 0,150" fill="var(--band-blue)"/>
      <polygon points="0,150 540,96 540,150" fill="var(--band-blue-dark)" opacity="0.25"/>
    </svg>

    <div class="contact contact__row">
      <span class="contact__item">
        <svg class="contact__icon" viewBox="0 0 24 24" aria-hidden="true"><path d="M6.6 10.8a15.1 15.1 0 0 0 6.6 6.6l2.2-2.2a1 1 0 0 1 1-.25 11.4 11.4 0 0 0 3.6.57 1 1 0 0 1 1 1V20a1 1 0 0 1-1 1A17 17 0 0 1 3 4a1 1 0 0 1 1-1h3.5a1 1 0 0 1 1 1c0 1.25.2 2.45.57 3.6a1 1 0 0 1-.25 1z"/></svg>
        0487650392
      </span>
      <span class="contact__item">
        <svg class="contact__icon" viewBox="0 0 24 24" aria-hidden="true"><path d="M2 5h20v14H2z M3.5 6.5 12 13l8.5-6.5" stroke="var(--band-blue)" stroke-width="1.6"/></svg>
        brightwayhaulandupkeep@mailbox.example
      </span>
    </div>
    <div class="contact contact__web">www.brightwayhaul.com.au</div>
  </section>

  <section class="card card--back" aria-label="Business card back">
    <div class="brand">
      <span class="brand__mark"></span>
      <span class="brand__name">Brightway Haul &amp; Upkeep Services</span>
    </div>

    <div class="services">
      <h2 class="services__title">Services we offer</h2>
      <ul class="service-list">
        <li><span class="service-list__label">CLEAN:</span><span>Windows, Gutters, Solar Panels, Driveways/paths, Carpets.</span></li>
        <li><span class="service-list__label">MOVE:</span><span>Small/medium Size House/office Moves, Large Item Pick-up &amp; Delivery, Yard Clean-up And Removal.</span></li>
      </ul>
      <p class="services__general">General maintenance and repairs.</p>
    </div>
  </section>

</body>
</html>
```